Brochure design

I have attached our current prospectus which has been created by ourselves, we are looking for this now to be professionally designed. We are happy to use the content but also for this to be amended to co-incide with the message on our website www.tumblewick.co.uk and for it to be condensed into a more reader friendly format. Whilst we are happy with this website, again it was created by ourselves and we are not necessarily following the same design features but the colour scheme should be similar to the website. The prospectus will be printed on 2 x A4 sheets folded to make an 8 page A5 booklet with page 1 being a front cover and page 8 being back cover with contact information. The business is a childrens day nursery so the prospectus should be bright, fun, to the point and informative. I am happy to provide any further information to designers who may be looking at this by emailing me dana@tumblewick.co.uk . The completed product should allow us to edit the text for example to communicate price changes.

Further information:

Tumblewick Nursery is very unique compared with other Nurseries. Most nurseries segregate age groups into different rooms whereas at Tumblewick aged groups mix together to create a homely environment and also children are not moving through different rooms every year. Could we therefore get a message through the prospectus which reflects this, we currently use a strapline "A unique home from home childcare experience" but we are looking to change this and will be grateful for ideas.

We have no preference whether stock images are used or our own, However, stock images and ours should not be included on the same page.

From the designs received we do like stock images for the front and back cover but these must be relevant, ie showing children aged 3 months old to 5 years old.

Target Market(s)

Mum's mainly but Dad's also of children aged 0 to 5 years old. Age range of parents between 22 and 45.

Industry/Entity Type

Environment

Font styles to use
Serif

Colors
acd036
b768aa
e9f1ce
ecdaeb
ceeae6

Requirements
Must have
• Fun, Colorfull, Bright, Concise, Informative.
Should not have
• Stock images and supplied images on the same pages

```html
<!DOCTYPE html>
<html lang="en">
<head>
<meta charset="utf-8">
<title>Pricing schedule</title>
<link href="https://fonts.googleapis.com/css2?family=Lobster&family=Jost:wght@400;600;700&family=Pathway+Gothic+One&display=swap" rel="stylesheet">
<style>
  :root {
    --green: #acd036;
    --purple: #b768aa;
    --green-soft: #e9f1ce;
    --pink-soft: #ecdaeb;
    --aqua-soft: #ceeae6;
    --ink: #1a1a1a;
    --paper: #ffffff;
  }
  * { margin: 0; padding: 0; box-sizing: border-box; }
  html, body { width: 860px; height: 1200px; overflow: hidden; background: var(--paper); }
  body { position: relative; font-family: "Jost", "Futura", sans-serif; color: var(--ink); }

  .side-pattern {
    position: absolute; top: 0; right: 0; width: 82px; height: 1200px;
    background: linear-gradient(180deg, var(--aqua-soft) 0%, var(--green-soft) 25%, var(--pink-soft) 50%, var(--aqua-soft) 75%, var(--green-soft) 100%);
  }

  .page-title {
    position: absolute; left: 30px; top: 14px;
    font-family: "Lobster", cursive; font-weight: 400;
    font-size: 58px; color: var(--purple); letter-spacing: 0.5px;
  }
  .intro {
    position: absolute; left: 30px; top: 98px; width: 740px;
    font-size: 20px; line-height: 27px;
  }

  .age-band { position: absolute; left: 0; width: 778px; padding: 12px 0 0 30px; }
  .age-band--under { top: 164px; height: 344px; background: var(--pink-soft); }
  .age-band--over { top: 512px; height: 338px; background: var(--green-soft); }

  .age-band h2 {
    font-size: 27px; font-weight: 700; color: var(--purple); line-height: 34px;
  }
  .price-row { display: grid; grid-template-columns: 216px 292px 120px; font-size: 21px; line-height: 30px; }
  .price-row span:last-child { padding-left: 0; }
  .price-row--extra { font-family: "Pathway Gothic One", sans-serif; font-size: 24px; grid-template-columns: 216px 292px 120px; }
  .price-row--extra span:last-child { font-family: "Jost", sans-serif; font-size: 21px; }
  .price-row--wide { font-family: "Pathway Gothic One", sans-serif; font-size: 24px; grid-template-columns: 508px 120px; }
  .price-row--wide span:last-child { font-family: "Jost", sans-serif; font-size: 21px; }
  .star { color: var(--purple); font-family: "Jost", sans-serif; font-size: 22px; }

  .note { position: absolute; left: 30px; top: 856px; font-size: 20px; }
  .funding-title {
    position: absolute; left: 30px; top: 888px;
    font-size: 28px; font-weight: 700; color: var(--green);
  }
  .terms-title {
    position: absolute; left: 30px; top: 938px;
    font-size: 27px; font-weight: 700; color: var(--green);
  }
  .terms {
    position: absolute; left: 30px; top: 972px; width: 740px;
    display: grid; grid-template-columns: 144px 1fr; row-gap: 0;
    font-size: 18.5px; line-height: 22px;
  }
</style>
</head>
<body>
  <div class="side-pattern" role="img" aria-label="Column of rounded squares in green, purple, aqua and pink"></div>

  <h1 class="page-title">Pricing schedule</h1>
  <p class="intro">September 2013: A non-refundable £50 Retainer Fee is charged to secure all bookings (after October 31st 2013)</p>

  <section class="age-band age-band--under">
    <h2>Under 3 year olds:</h2>
    <div class="price-row"><span>Session</span><span>Time</span><span>Price</span></div>
    <div class="price-row"><span>Morning</span><span>7.30am-12pm</span><span>£22.00</span></div>
    <div class="price-row"><span>Afternoon</span><span>1pm-6.30pm</span><span>£22.00</span></div>
    <div class="price-row"><span>Full Day</span><span>7.30am-6.30pm</span><span>£40.00</span></div>
    <div class="price-row"><span>Full Week</span><span>Full Day/5 Days</span><span>£180.00</span></div>
    <div class="price-row"><span>School Day</span><span>9.30am-4.00pm</span><span>£37.00</span></div>
    <div class="price-row"><span>Full School Week</span><span>School Day/5 Days</span><span>£170.00</span></div>
    <div class="price-row price-row--wide"><span><span class="star">*</span>Additional hours (ad hoc)7.30am-9.30am</span><span>£9.00</span></div>
    <div class="price-row price-row--wide"><span>12pm-1pm, 4.00pm-5.00pm, 5.00pm-6.00pm</span><span>£4.50</span></div>
  </section>

  <section class="age-band age-band--over">
    <h2>Over 3 year olds</h2>
    <div class="price-row"><span>Session</span><span>Time</span><span>Price</span></div>
    <div class="price-row"><span>Morning</span><span>7.30am-12pm</span><span>£20.00</span></div>
    <div class="price-row"><span>Afternoon</span><span>1pm-6.30pm</span><span>£20.00</span></div>
    <div class="price-row"><span>Full Day</span><span>7.30am-6.30pm</span><span>£38.00</span></div>
    <div class="price-row"><span>Full Week</span><span>Full Day/5 Days</span><span>£170.00</span></div>
    <div class="price-row"><span>School Day</span><span>9.30am-4.00pm</span><span>£36.00</span></div>
    <div class="price-row"><span>Full School Week</span><span>School Day/5 Days</span><span>£160.00</span></div>
    <div class="price-row price-row--wide"><span><span class="star">*</span>Additional hours(ad hoc)7.30am-9.30am</span><span>£7.00</span></div>
    <div class="price-row price-row--wide"><span>12pm-1pm, 4.00pm-5.00pm, 5.00pm-6.00pm</span><span>£4.00</span></div>
  </section>

  <p class="note"><span class="star">*</span>Ad hoc hours are subject to availability</p>
  <h2 class="funding-title">FEEE Funding (3 and 4 year olds only)</h2>
  <h2 class="terms-title">Terms and conditions</h2>
  <div class="terms">
    <span>FEEE session</span>
    <span>9.00am – 12.00am/1.00pm-4.00pm<br>Term time only (no registration fee required,<br>but subject to availability)</span>
    <span>OR</span>
    <span>FEEE can be used over our normal sessions at a specified time of a minimum of 2.5 hrs or up to 10 hours per day for a maximum of 15 hours per week, term time only (normal prices apply outside of the 38 weeks and registration fee required)</span>
  </div>
</body>
</html>
```